Small environmental consultancy needs a simple but professional web design

We are a boutique environmental consultancyand contracting business located in Margaret River in the South West of Western Australia.

We have two arms
1) Consulting which offers environmental planning, management and assessment services primarily to local government and the development industry.
2) Contracting which implements on site plans and on ground works primarily involving revegetation, bush regeneration and environmental weed control.

We need a simple yet professional web design within the wordpress platform that commmunicates professionalism, experience and technical expertise without appearing too corporate.

Something like this structure appeals:
http://fernquill.net.au/environment-services/
or
http://www.tallowbrookenvironmental.com.au/index.php

(without the image gallery function)

Target Market(s)

Local Government Officers deciding on tenders;
Developers, Engineers, Town Planning consultants looking for environmental expertise

Industry/Entity Type

Business

Number of Pages Required

5+ page

Font styles to use
Sans Serif

Colors
33a6d7
9bcb3c

Requirements
Must have
• Pages required include:
• Home
• Environmental Planning and Management
• Revegetation and Regeneration Implementation (This page can mirror the Environmental Planning and Management page exactly in structure but with different text and images)
• About Us (I think that this page can be relatively simple and generic)
• Contact (I think that this page can be very simple and generic)
Nice to have
• An ability to start out basic and quicikly establish a website presence and then build in additional drop downs and pages over time.
Should not have
• It does not need a photo gallery page;
• It does not need a major amount of space dedicated to social media and blogs etc as this is not currently particularly active area for us

```html
<!DOCTYPE html>
<html lang="en">
<head>
<meta charset="utf-8">
<title>About Us – Wandoo Ecoservices</title>
<link rel="stylesheet" href="https://fonts.googleapis.com/css2?family=Open+Sans:wght@400;600;700&family=Raleway:wght@700&family=Teko:wght@400;500&display=swap">
<style>
  :root{
    --blue:#33a6d7;
    --blue-dark:#1f86c1;
    --green:#9bcb3c;
    --green-dark:#7fa82a;
    --brown:#6b4424;
    --text:#555555;
    --heading-dark:#333333;
    --header-bg:#f1f1f1;
    --footer-bg:#ebebeb;
    --line:#d9d9d9;
    --white:#ffffff;
    --placeholder:#aaaaaa;
  }
  *{box-sizing:border-box;margin:0;padding:0}
  html,body{width:1063px;height:1200px;overflow:hidden}
  body{position:relative;background:var(--white);font-family:"Open Sans",Arial,sans-serif;color:var(--text)}

  /* Header */
  .site-header{position:absolute;left:0;top:0;width:1063px;height:155px;background:var(--header-bg)}
  .brand{position:absolute;left:65px;top:42px;display:flex;align-items:center;gap:16px}
  .brand-mark{width:62px;height:62px;border-radius:50%;background:var(--green)}
  .brand-name{font-family:"Open Sans",sans-serif;font-weight:600;font-size:32px;color:var(--brown);letter-spacing:.3px}
  .call-top{position:absolute;right:63px;top:32px;text-align:left}
  .call-top .label{font-weight:700;font-size:15px;color:#111}
  .call-top .number{font-weight:700;font-size:24px;color:var(--blue);line-height:1.1}
  .search{position:absolute;left:809px;top:93px;width:188px;height:25px;background:var(--white);border:1px solid #e2e2e2;display:flex;align-items:center;justify-content:space-between;padding:0 6px 0 8px;font-size:12.5px;color:#666}

  /* Nav */
  .main-nav{position:absolute;left:0;top:155px;width:1063px;height:38px;background:var(--blue);border-bottom:3px solid #2b95c6}
  .main-nav ul{list-style:none;display:flex;height:35px;padding-left:70px}
  .main-nav li{font-family:"Raleway",sans-serif;font-weight:700;font-size:12.5px;color:var(--white);text-transform:uppercase;display:flex;align-items:center;padding:0 19px}
  .main-nav li.current{background:var(--blue-dark)}

  /* Banner */
  .banner{position:absolute;left:0;top:193px;width:1063px;height:113px;
    background:linear-gradient(180deg,#8fb7dc 0%,#c9dced 35%,#5f6d4d 55%,#1f5b84 78%,#2c6f98 100%)}

  /* Content */
  .content{position:absolute;left:65px;top:340px;width:932px}
  .page-title{font-family:"Teko",sans-serif;font-weight:500;font-size:38px;color:var(--green);line-height:1;letter-spacing:.3px}
  .content p{font-size:12.2px;line-height:18.8px;margin-bottom:18.8px}
  .intro{display:flex;justify-content:space-between;margin-top:19px}
  .intro-text{width:533px}
  .feature-photo{width:373px;height:253px;margin-top:1px;
    background:linear-gradient(135deg,#4f7a3a 0%,#e99a2a 35%,#f0b23a 50%,#6a2f6e 70%,#3d6a34 100%)}
  .content .intro-text p:last-child{margin-bottom:17px}

  /* Footer */
  .site-footer{position:absolute;left:0;top:909px;width:1063px;height:291px;background:var(--footer-bg);border-top:1px solid var(--line)}
  .footer-heading{font-family:"Teko",sans-serif;font-weight:400;font-size:20px;color:var(--heading-dark);line-height:1;text-transform:uppercase}
  .footer-col{position:absolute;top:27px;font-size:12px;line-height:18px;color:#444}
  .col-about{left:65px}
  .col-web{left:334px}
  .col-contact{left:544px;width:453px}
  .footer-col ul{list-style:none;margin-top:10px}
  .footer-col .url{margin-top:10px}
  .call-now{position:absolute;left:64px;top:138px}
  .call-now .footer-heading{font-size:19px}
  .call-now .number{display:flex;align-items:center;gap:6px;font-family:"Teko",sans-serif;font-weight:500;font-size:32px;color:var(--green);line-height:1;margin-top:4px}
  .contact-form{margin-top:14px;display:grid;grid-template-columns:222px 223px;column-gap:8px;row-gap:8px}
  .field{height:33px;background:var(--white);border:1px solid #dcdcdc;display:flex;align-items:center;justify-content:space-between;padding:0 8px 0 12px;font-size:13px;color:var(--placeholder)}
  .field.message{grid-column:1 / 3;height:65px;align-items:flex-start;padding-top:8px}
  .send{grid-column:1;width:138px;height:39px;background:linear-gradient(180deg,#9bcb3c,#6f9a22);color:var(--white);font-family:"Teko",sans-serif;font-size:19px;display:flex;align-items:center;justify-content:center;text-transform:uppercase}
  .footer-bottom{position:absolute;left:65px;right:43px;top:246px;border-top:1px solid #dddddd;padding-top:12px;font-size:12px;color:#444}
</style>
</head>
<body>
  <header class="site-header">
    <div class="brand">
      <span class="brand-mark"></span>
      <span class="brand-name">Wandoo Ecoservices</span>
    </div>
    <div class="call-top">
      <div class="label">Call Us</div>
      <div class="number">0400 382 617</div>
    </div>
    <div class="search">
      <span>Search</span>
      <svg width="14" height="14" viewBox="0 0 14 14" aria-hidden="true"><circle cx="6" cy="6" r="4.5" fill="none" stroke="#999" stroke-width="1.6"/><line x1="9.3" y1="9.3" x2="13" y2="13" stroke="#999" stroke-width="1.8"/></svg>
    </div>
  </header>

  <nav class="main-nav">
    <ul>
      <li>Home</li>
      <li>Environmental Planning and Management</li>
      <li>Revegetation and Bush Regeneration</li>
      <li class="current">About Us</li>
      <li>Contact</li>
    </ul>
  </nav>

  <div class="banner" role="img" aria-label="Panoramic coastal landscape with rocky shore, headland and blue sky"></div>

  <main class="content">
    <h1 class="page-title">ABOUT US</h1>
    <div class="intro">
      <div class="intro-text">
        <p>Lorem ipsum dolor sit amet, consectetuer adipiscing elit, sed diam nonummy nibh euismod tincidunt ut laoreet dolore magna aliquam erat ullamcorper suscipit lobortis nisl ut aliquip ex ea commodo consequat. Lorem ipsum dolor sit amet, consectetuer adipiscing elit, sed diam nonummy nibh euismod tincidunt ut laoreet dolore magna aliquam erat volutpat. Ut wisi enim ad minim veniam, quis nostrud exerci tation ullamcorper suscipit lobortis nisl ut aliquip ex ea commodo consequat.Lorem ipsum dolor sit amet, consectetuer adipiscing elit, sed diam nonummy nibh euismod tincidunt ut laoreet dolore magna aliquam erat volutpat. Ut wisi enim ad minim veniam, quis nostrud exerci tation ullamcorper suscipit lobortis nisl ut aliquip ex ea commodo consequat.</p>
        <p>Lorem ipsum dolor sit amet, consectetuer adipiscing elit, sed diam nonummy nibh euismod tincidunt ut laoreet dolore magna aliquam erat volutpat. Ut wisi enim ad minim veniam, quis nostrud exerci tation ullamcorper suscipit lobortis nisl ut aliquip ex ea commodo consequat. Lorem ipsum dolor sit amet, consectetuer adipiscing elit, sed diam nonummy nibh euismod tincidunt ut laoreet dolore magna aliquam erat ullamcorper suscipit lobortis nisl ut aliquip ex ea commodo consequat.</p>
      </div>
      <div class="feature-photo" role="img" aria-label="Close-up of orange and purple native pea flowers among green leaves"></div>
    </div>
    <p>Lorem ipsum dolor sit amet, consectetuer adipiscing elit, sed diam nonummy nibh euismod tincidunt ut laoreet dolore magna aliquam erat ullamcorper suscipit lobortis nisl ut aliquip ex ea commodo consequat. Lorem ipsum dolor sit amet, consectetuer adipiscing elit, sed diam nonummy nibh euismod tincidunt ut laoreet dolore magna aliquam erat volutpat. Ut wisi enim ad minim veniam, quis nostrud exerci tation ullamcorper suscipit lobortis nisl ut aliquip ex ea commodo consequat.Lorem ipsum dolor sit amet, consectetuer adipiscing elit, sed diam nonummy nibh euismod tincidunt ut laoreet dolore magna aliquam erat volutpat. Ut wisi enim ad minim veniam, quis nostrud exerci tation ullamcorper suscipit lobortis nisl ut aliquip ex ea commodo consequat.</p>
    <p>Lorem ipsum dolor sit amet, consectetuer adipiscing elit, sed diam nonummy nibh euismod tincidunt ut laoreet dolore magna aliquam erat volutpat. Ut wisi enim ad minim veniam, quis nostrud exerci tation ullamcorper suscipit lobortis nisl ut aliquip ex ea commodo consequat. Lorem ipsum dolor sit amet, consectetuer adipiscing elit, sed diam nonummy nibh euismod tincidunt ut laoreet dolore magna aliquam erat ullamcorper suscipit lobortis nisl ut aliquip ex ea commodo consequat.</p>
  </main>

  <footer class="site-footer">
    <div class="footer-col col-about">
      <h2 class="footer-heading">About</h2>
      <ul>
        <li>Environmental Planning and Management</li>
        <li>Revegetation and Bush Regeneration</li>
        <li>Contacts</li>
      </ul>
    </div>
    <div class="call-now">
      <h2 class="footer-heading">Call us now:</h2>
      <div class="number">
        <svg width="20" height="20" viewBox="0 0 20 20" aria-hidden="true"><path d="M4 2.5l3 0 1.5 4-2 1.5c1 2.2 2.6 3.8 4.8 4.8l1.5-2 4 1.5 0 3c0 1-1 2-2 2C8.5 17.3 2.7 11.5 2 4.5c0-1 1-2 2-2z" fill="#444"/></svg>
        <span>0400 382 617</span>
      </div>
    </div>
    <div class="footer-col col-web">
      <h2 class="footer-heading">Website</h2>
      <div class="url">www.wandooecoservices.com.au</div>
    </div>
    <div class="footer-col col-contact">
      <h2 class="footer-heading">Contact us</h2>
      <div class="contact-form">
        <div class="field"><span>Name</span>
          <svg width="18" height="18" viewBox="0 0 18 18" aria-hidden="true"><circle cx="9" cy="5.5" r="4" fill="#b5b5b5"/><path d="M1.5 18c0-5 3.4-7.5 7.5-7.5s7.5 2.5 7.5 7.5z" fill="#b5b5b5"/></svg>
        </div>
        <div class="field"><span>E-mail</span>
          <svg width="20" height="14" viewBox="0 0 20 14" aria-hidden="true"><rect width="20" height="14" rx="1.5" fill="#b5b5b5"/><path d="M1 1.5l9 6.5 9-6.5" fill="none" stroke="#fff" stroke-width="1.5"/></svg>
        </div>
        <div class="field message"><span>Message</span>
          <svg width="19" height="17" viewBox="0 0 19 17" aria-hidden="true"><path d="M1 1h17v11H7l-4 4v-4H1z" fill="#b5b5b5"/><circle cx="5.5" cy="6.5" r="1.2" fill="#fff"/><circle cx="9.5" cy="6.5" r="1.2" fill="#fff"/><circle cx="13.5" cy="6.5" r="1.2" fill="#fff"/></svg>
        </div>
        <div class="send">Send message</div>
      </div>
    </div>
    <div class="footer-bottom">© 2015 Wandoo Ecoservices. All Rights Reserved.</div>
  </footer>
</body>
</html>
```